Mira Ellsworth ADHD coach needs a flyer

I need a flyer to be sent by email. the copy is attached. It can be changed/reduced to fit the flyer. I would like to keep my website colors. My website is www.miraellsworth.net - Thank you!

```html
<!DOCTYPE html>
<html lang="en">
<head>
<meta charset="utf-8">
<title>Mira Ellsworth – Academic Success Coaching Flyer</title>
<link href="https://fonts.googleapis.com/css2?family=Arimo:ital,wght@0,400;0,700;1,400&family=Work+Sans:wght@400;500;600&display=swap" rel="stylesheet">
<style>
  :root{
    --page:#e9e6e0;
    --paper:#f5f4ef;
    --teal:#7aa5ae;
    --teal-dark:#66929b;
    --teal-soft:#a9c6cc;
    --panel:#e4e4e0;
    --ink:#2b2f31;
    --white:#ffffff;
  }
  *{box-sizing:border-box;margin:0;padding:0}
  html,body{width:1200px;height:900px;overflow:hidden;background:var(--page)}
  body{font-family:"Work Sans",sans-serif;color:var(--ink)}
  .flyer{position:absolute;left:290px;top:12px;width:620px;height:876px;background:var(--paper);overflow:hidden;box-shadow:0 2px 10px rgba(0,0,0,.12)}
  .header-band{position:absolute;left:0;top:0;width:620px;height:300px;background:var(--teal)}
  .photo-backdrop{position:absolute;left:0;top:300px;width:290px;height:130px;background:var(--teal)}
  .title{position:absolute;left:250px;top:26px;width:350px;font-family:"Arimo",sans-serif;font-weight:700;font-size:30px;line-height:1.05;color:var(--white)}
  .subtitle{position:absolute;left:250px;top:100px;width:345px;font-family:"Arimo",sans-serif;font-style:italic;font-size:10.5px;line-height:1.35;color:#e3eef0}
  .portrait{position:absolute;left:18px;top:120px;width:250px;height:310px;background:linear-gradient(160deg,#9fbcc2 0%,#d9c7c6 45%,#3b2f3f 100%)}
  .intro-panel{position:absolute;left:262px;top:150px;width:340px;height:262px;background:var(--panel);border-radius:22px;padding:16px 18px;font-size:8.6px;line-height:1.5}
  .intro-panel p+p{margin-top:8px}
  .band{position:absolute;height:30px;background:var(--teal);color:var(--white);font-family:"Arimo",sans-serif;font-weight:700;font-size:13px;line-height:1.1;display:flex;align-items:center;padding:0 12px;gap:8px}
  .band.tall{height:42px}
  .chevrons{letter-spacing:-1px;font-size:11px;flex:none}
  .band-help{left:20px;top:440px;width:280px}
  .band-have{left:318px;top:428px;width:282px}
  .band-real{left:20px;top:752px;width:280px;font-size:12px}
  .col{position:absolute;font-size:8.4px;line-height:1.45}
  .col-left{left:24px;top:490px;width:272px}
  .col-left p{margin-bottom:5px}
  .arrow-list{list-style:none}
  .arrow-list li{position:relative;padding-left:11px;margin-bottom:2px}
  .arrow-list li::before{content:"";position:absolute;left:0;top:4px;border-left:6px solid var(--teal);border-top:3.5px solid transparent;border-bottom:3.5px solid transparent}
  .dot-list{list-style:none}
  .dot-list li{position:relative;padding-left:11px}
  .dot-list li::before{content:"•";position:absolute;left:1px}
  .gains{left:26px;top:802px;width:270px}
  .have-list{left:324px;top:466px;width:270px}
  .quote-box{position:absolute;border-radius:14px;padding:10px 14px;font-size:8.3px;line-height:1.42}
  .parents{left:318px;top:532px;width:282px;height:128px;background:var(--panel)}
  .students{left:318px;top:668px;width:282px;height:148px;background:var(--teal);color:var(--white)}
  .quote-box h3{font-family:"Arimo",sans-serif;font-size:11px;text-align:center;margin-bottom:6px}
  .quote{position:relative;padding-left:14px;margin-bottom:6px}
  .quote::before{content:"\201C";position:absolute;left:0;top:-3px;font-family:"Arimo",sans-serif;font-weight:700;font-size:15px}
  .next-steps{position:absolute;left:318px;top:822px;width:282px;text-align:center;font-size:8.4px;line-height:1.4}
  .next-steps h3{font-family:"Arimo",sans-serif;font-size:11px}
  .next-steps strong{font-weight:600}
</style>
</head>
<body>
<article class="flyer">
  <div class="header-band"></div>
  <div class="photo-backdrop"></div>
  <div class="portrait" role="img" aria-label="Portrait photo of coach Mira Ellsworth in a light blazer, arms crossed"></div>

  <h1 class="title">Helping Your Child with ADHD or Other Learning</h1>
  <p class="subtitle">Academic success coaching that leads to lifelong transformation for students with ADHD and similar challenges that may have impeded their ability to thrive.</p>

  <section class="intro-panel">
    <p>Sending your child off to college can feel scary, especially if that college is hundreds of miles away. You worry about how they’ll do on their own—whether they’ll make friends, earn good grades, and be happy—especially without you there to support them daily. You know your child is bright, and you want them to have a great future, but you’re concerned they will struggle without the right support and resources.</p>
    <p>You don’t need to feel helpless as you send your child off to this next stage of their lives. Mira is dedicated to making that transition easier for everyone. Mira Ellsworth has years of experience helping students thrive despite their challenges. She sees your child’s potential and helps them see it, too. She provides a safety net as they adjust to a new environment at college. Her services are comprehensive and adaptable, based on the requirements of each individual: helping with course selection and scheduling, time management, study strategies, focus, making new friends, and adapting to change. Through it all, Mira guides students through fundamental work on mindset to ensure that changes stick.</p>
  </section>

  <h2 class="band band-help tall"><span class="chevrons">»»»»</span><span>Empowering Focus:<br>How Mira Helps</span></h2>
  <div class="col col-left">
    <p>Mira has taken students from failing to a 3.0 GPA, and from a C student to the Dean’s List, in just one semester. It doesn’t take years to provide lasting results; all it takes is the right guide.</p>
    <p>Uniquely positioned to help your child, Mira:</p>
    <ul class="arrow-list">
      <li>Tailors support so that your child improves focus and maximizes their potential in college and beyond.</li>
      <li>Understands your child’s unique needs - she sees the gifts that others often miss.</li>
      <li>Knows the academic landscape intimately, including the challenges faced by students with ADHD and other conditions.</li>
      <li>Helps with the logistics of scheduling in a way that most advisors can’t, enrolling students in the courses that best suit their learning style.</li>
      <li>Nurtures the brilliance in your bright child.</li>
      <li>Provides a balance between encouraging students and challenging them.</li>
    </ul>
  </div>

  <h2 class="band band-real tall"><span class="chevrons">»»»</span><span>Realizing Potential: The Transformation<br>You’ll See in Your Child</span></h2>
  <ul class="col dot-list gains">
    <li>A mindset of self-belief and increased confidence.</li>
    <li>Higher grades and the drive to graduate.</li>
    <li>Social integration and making friends.</li>
    <li>Happiness and fulfilment.</li>
    <li>A deep sense of personal achievement and pride.</li>
  </ul>

  <h2 class="band band-have"><span class="chevrons">»»»»</span><span>You Will Have:</span></h2>
  <ul class="col dot-list have-list">
    <li>Less stress, knowing that your child is in good hands.</li>
    <li>Fewer sleepless nights worrying about your child.</li>
    <li>Confidence that they are receiving the right support.</li>
    <li>Joy and pride at seeing them do well.</li>
  </ul>

  <section class="quote-box parents">
    <h3>What Parents Say</h3>
    <p class="quote">Mira was the glue that kept our daughter in college... as our daughter’s Academic Coach, [she] gave our daughter the ability to finish strong by empowering her with the skills needed to be successful.” - Renee</p>
    <p class="quote">Mira has always told my daughter not that she can succeed, but that she will succeed!”—Marla</p>
  </section>

  <section class="quote-box students">
    <h3>What Students Say</h3>
    <p class="quote">Last semester I completed all 16 hours and I had the highest GPA I’ve ever had!” —Former student</p>
    <p class="quote">Under her instruction, my grades began to improve. I ended up making the Dean’s List during my time at Harlow State, and I was also inducted into the Civic Honor Society. I am currently in my first year of law school at Crestview University, a top tier school.”—Former student</p>
  </section>

  <footer class="next-steps">
    <h3>Next Steps</h3>
    <p>To learn more and discuss your child’s individual needs, call <strong>555 014 2237</strong> or email <strong>coach@miraellsworth.net</strong></p>
  </footer>
</article>
</body>
</html>
```